Business Card Design Project

restaurant management company needs business card design.

Industry/Entity Type

Restaurant

Requirements
Must have
• our logo
bramble den logo
QLW logo
WrapNest Logo
Nice to have
• Morley Quint
(position)

238 Halvey Street
Larchmere XK,
Canada
E3K 2R8

Tel 555-xxx-xxxx Ext 348
Fax 555-xxx-xxxx
Mobile 555-xxx-xxxx

morleyquint@kbrholdings.example
Should not have
• Morley Quint
(position)

238 Halvey Street
Larchmere XK,
Canada
E3K 2R8

Tel 555-xxx-xxxx Ext 348
Fax 555-xxx-xxxx
Mobile 555-xxx-xxxx

morleyquint@kbrholdings.example

```html
<!DOCTYPE html>
<html lang="en">
<head>
<meta charset="utf-8">
<title>ZLM Hospitality – Business Cards</title>
<link href="https://fonts.googleapis.com/css2?family=Open+Sans:wght@300;400;600;800&display=swap" rel="stylesheet">
<style>
  :root {
    --bg: #e8e8e8;
    --red: #ff0000;
    --ink: #111111;
    --ink-soft: #333333;
    --white: #ffffff;
    --rim: #8a8a8a;
  }
  html, body {
    margin: 0;
    width: 1200px;
    height: 903px;
    overflow: hidden;
    background: var(--bg);
    font-family: "Open Sans", sans-serif;
  }
  .stage { position: relative; width: 1200px; height: 903px; }
  .card {
    position: absolute;
    left: 337px;
    width: 575px;
    height: 328px;
    filter: drop-shadow(0 2px 3px rgba(0,0,0,0.25));
  }
  .card--front { top: 109px; }
  .card--back  { top: 491px; }
  .card svg { display: block; width: 100%; height: 100%; }

  .brand-mark { font-weight: 800; font-size: 66px; letter-spacing: -1px; }
  .brand-sub  { font-weight: 600; font-size: 9.5px; }
  .person-name  { font-weight: 600; font-size: 27px; fill: var(--red); }
  .person-title { font-weight: 300; font-size: 18px; }
  .contact { font-weight: 300; font-size: 18px; text-anchor: end; }
  .contact .label { fill: var(--red); }
  .partner { font-weight: 600; font-size: 15px; text-anchor: middle; }

  .on-light { fill: var(--ink); }
  .on-light-soft { fill: var(--ink-soft); }
  .on-dark { fill: var(--white); }
</style>
</head>
<body>
<div class="stage">

  <!-- Front: light left, dark panel right -->
  <div class="card card--front">
    <svg viewBox="0 0 702 401" xmlns="http://www.w3.org/2000/svg">
      <defs>
        <clipPath id="front-shape"><rect width="702" height="401" rx="26"/></clipPath>
        <linearGradient id="front-paper" x1="0" y1="0" x2="0" y2="1">
          <stop offset="0" stop-color="#f1f1f1"/>
          <stop offset="0.45" stop-color="#ffffff"/>
        </linearGradient>
        <radialGradient id="front-panel" cx="0.3" cy="0.45" r="0.75">
          <stop offset="0" stop-color="#454545"/>
          <stop offset="1" stop-color="#000000"/>
        </radialGradient>
      </defs>
      <g clip-path="url(#front-shape)">
        <rect width="702" height="401" fill="url(#front-paper)"/>
        <circle class="rim" cx="577" cy="200" r="267" fill="var(--rim)"/>
        <circle class="swoosh" cx="587" cy="200" r="267" fill="var(--red)"/>
        <circle class="panel" cx="590" cy="267" r="242" fill="url(#front-panel)"/>
      </g>

      <text class="brand-mark on-light" x="64" y="132">ZLM</text>
      <text class="brand-sub on-light" x="67" y="146">Zelmor Hospitality Inc</text>

      <text class="person-name" x="64" y="295">Morley Quint</text>
      <text class="person-title on-light-soft" x="64" y="322">Marketing Manager</text>

      <g class="contact on-dark">
        <text x="675" y="92">238 Halvey Street</text>
        <text x="675" y="115">Larchmere XK,</text>
        <text x="675" y="138">Canada E3K 2R8</text>
        <text x="675" y="186"><tspan class="label">p.</tspan> 555-xxx-xxxx Ext 348</text>
        <text x="675" y="209"><tspan class="label">f.</tspan> 555-xxx-xxxx</text>
        <text x="675" y="232"><tspan class="label">m.</tspan> 555-xxx-xxxx</text>
        <text x="675" y="256"><tspan class="label">e.</tspan> morleyquint@kbrholdings.example</text>
      </g>

      <g class="partners">
        <text class="partner on-dark" x="440" y="346">bramble den</text>
        <circle cx="546" cy="339" r="37" fill="var(--red)"/>
        <text class="partner on-dark" x="546" y="345">QLW</text>
        <text class="partner on-dark" x="642" y="346">WrapNest</text>
      </g>
    </svg>
  </div>

  <!-- Back: dark left, light panel right -->
  <div class="card card--back">
    <svg viewBox="0 0 702 401" xmlns="http://www.w3.org/2000/svg">
      <defs>
        <clipPath id="back-shape"><rect width="702" height="401" rx="26"/></clipPath>
        <radialGradient id="back-paper" cx="0.36" cy="0.55" r="0.45">
          <stop offset="0" stop-color="#444444"/>
          <stop offset="1" stop-color="#000000"/>
        </radialGradient>
      </defs>
      <g clip-path="url(#back-shape)">
        <rect width="702" height="401" fill="url(#back-paper)"/>
        <circle class="rim" cx="577" cy="200" r="267" fill="var(--rim)"/>
        <circle class="swoosh" cx="587" cy="200" r="267" fill="var(--red)"/>
        <circle class="panel" cx="590" cy="267" r="242" fill="var(--white)"/>
      </g>

      <text class="brand-mark on-dark" x="64" y="132">ZLM</text>
      <text class="brand-sub on-dark" x="67" y="146">Zelmor Hospitality Inc</text>

      <text class="person-name" x="64" y="295">Morley Quint</text>
      <text class="person-title on-dark" x="64" y="322">Marketing Manager</text>

      <g class="contact on-light-soft">
        <text x="675" y="92">238 Halvey Street</text>
        <text x="675" y="115">Larchmere XK,</text>
        <text x="675" y="138">Canada E3K 2R8</text>
        <text x="675" y="186"><tspan class="label">p.</tspan> 555-xxx-xxxx Ext 348</text>
        <text x="675" y="209"><tspan class="label">f.</tspan> 555-xxx-xxxx</text>
        <text x="675" y="232"><tspan class="label">m.</tspan> 555-xxx-xxxx</text>
        <text x="675" y="256"><tspan class="label">e.</tspan> morleyquint@kbrholdings.example</text>
      </g>

      <g class="partners">
        <text class="partner on-light" x="440" y="346">bramble den</text>
        <circle cx="546" cy="339" r="37" fill="var(--red)"/>
        <text class="partner on-dark" x="546" y="345">QLW</text>
        <text class="partner on-light" x="642" y="346">WrapNest</text>
      </g>
    </svg>
  </div>

</div>
</body>
</html>
```